Northfield Builders Guild Business card

We are looking for a new business card design with photo included.
Our business is a nonprofit construction contractor membership organization. We offer business education, assist with business setup and licensing, provide safety training, and provide a member directory.
URL: www.builderslinkguild.org
Color code:
CMYK: 0 cyan, 42 magenta, 100 yellow, 0 black for Print.
Hexidecimal: #FF9900
RGB: R 255; G 153; B 0

```html
<!DOCTYPE html>
<html lang="en">
<head>
<meta charset="utf-8">
<title>Northfield Builders Guild – Business Card</title>
<link rel="stylesheet" href="https://fonts.googleapis.com/css2?family=Arimo:wght@400;700&family=Oswald:wght@500&display=swap">
<style>
  :root {
    --page: #0d0d0d;
    --card: #1b1b1b;
    --orange: #ff9900;
    --white: #ffffff;
    --rule: #6a6a6a;
  }
  * { box-sizing: border-box; margin: 0; padding: 0; }
  html, body { width: 1200px; height: 900px; overflow: hidden; background: var(--page); }
  .canvas {
    width: 1200px; height: 900px;
    display: flex; flex-direction: column; align-items: center; justify-content: center; gap: 40px;
    font-family: "Arimo", Arial, sans-serif;
  }
  .card {
    position: relative;
    width: 560px; height: 320px;
    background: var(--card);
    box-shadow: 0 10px 30px rgba(0,0,0,.6);
    overflow: hidden;
  }
  .card__band {
    position: absolute; left: 0; right: 0; bottom: 0; height: 8px;
    background: var(--orange);
  }
  /* Front */
  .card--front { display: flex; flex-direction: column; align-items: center; }
  .brand {
    margin-top: 118px;
    font-weight: 700; font-size: 30px; letter-spacing: 1px;
    color: var(--white); text-transform: uppercase;
  }
  .website {
    position: absolute; bottom: 34px; left: 0; right: 0; text-align: center;
    font-size: 15px; color: var(--white); letter-spacing: .3px;
  }
  .website__domain { color: var(--orange); }
  /* Back */
  .person {
    position: absolute; left: 52px; top: 96px; width: 190px;
  }
  .person__name {
    font-family: "Oswald", "Arial Narrow", sans-serif; font-weight: 500;
    font-size: 30px; line-height: 1.05; color: var(--orange); text-transform: uppercase;
  }
  .person__title {
    margin-top: 4px; font-size: 12.5px; color: var(--white); letter-spacing: .5px; text-transform: uppercase;
  }
  .divider {
    position: absolute; left: 262px; top: 92px; width: 1px; height: 92px; background: var(--rule);
  }
  .contacts {
    position: absolute; left: 282px; top: 92px; list-style: none;
  }
  .contacts__item {
    display: flex; align-items: center; gap: 8px;
    font-size: 14px; color: var(--white); height: 23px;
  }
  .contacts__icon { width: 18px; height: 18px; flex: none; }
  .contacts__note { color: var(--orange); }
  .address {
    position: absolute; left: 0; right: 0; bottom: 34px; text-align: center;
    font-size: 15px; color: var(--white); letter-spacing: .3px;
  }
</style>
</head>
<body>
<main class="canvas">

  <section class="card card--front" aria-label="Card front">
    <h1 class="brand">Northfield Builders Guild</h1>
    <p class="website">www.<span class="website__domain">builderslinkguild</span>.org</p>
    <div class="card__band"></div>
  </section>

  <section class="card card--back" aria-label="Card back">
    <div class="person">
      <h2 class="person__name">Daniel Hartley</h2>
      <p class="person__title">Managing Director</p>
    </div>
    <div class="divider"></div>
    <ul class="contacts">
      <li class="contacts__item">
        <svg class="contacts__icon" viewBox="0 0 18 18" aria-hidden="true"><circle cx="9" cy="9" r="9" fill="#ff9900"/><path d="M6 4.5l1.6 2-1 1.1a6 6 0 0 0 3.8 3.8l1.1-1 2 1.6-1 1.5C9 13.5 4.5 9 4.5 5.5z" fill="#1b1b1b"/></svg>
        <span>(555) 214-7380 <span class="contacts__note">(Office)</span></span>
      </li>
      <li class="contacts__item">
        <svg class="contacts__icon" viewBox="0 0 18 18" aria-hidden="true"><circle cx="9" cy="9" r="9" fill="#ff9900"/><rect x="6" y="4" width="6" height="10" rx="1" fill="none" stroke="#1b1b1b" stroke-width="1.4"/></svg>
        <span>800-555-0172</span>
      </li>
      <li class="contacts__item">
        <svg class="contacts__icon" viewBox="0 0 18 18" aria-hidden="true"><circle cx="9" cy="9" r="9" fill="#ff9900"/><rect x="6" y="4" width="6" height="3" fill="#1b1b1b"/><rect x="4" y="7.5" width="10" height="4.5" rx="1" fill="#1b1b1b"/><rect x="6" y="11" width="6" height="3" fill="#1b1b1b"/></svg>
        <span>555.301.4426</span>
      </li>
      <li class="contacts__item">
        <svg class="contacts__icon" viewBox="0 0 18 18" aria-hidden="true"><circle cx="9" cy="9" r="9" fill="#ff9900"/><rect x="4.5" y="5.5" width="9" height="7" fill="#1b1b1b"/><path d="M4.5 5.5L9 9.5l4.5-4" fill="none" stroke="#ff9900" stroke-width="1"/></svg>
        <span>hello@nbguild.org</span>
      </li>
    </ul>
    <p class="address">2400 Cedar Ridge Ave, Suite #210, Fairview, OR 97024</p>
    <div class="card__band"></div>
  </section>

</main>
</body>
</html>
```